Business Card for Professional Photographer

I'm looking for an eye catching modern clean design that compliments my logo/ website fonts & colours.
I specialise in architecture, corporate & commercial photography so I'm marketing to professional clients rather than portrait / wedding clients.

I would prefer to not have a solid black design.

My logo brand guide is as follows :

Main front font. : Reislust
Main font colour : #fff
Slogan front font : Ubuntu Bold
Monogram front font : Venti Medium
Container colour : #fff

I need print ready files in pdf .png & .eps formats.

Included in the files below are some screen grabs as reference to font & colours etc.

```html
<!DOCTYPE html>
<html lang="en">
<head>
<meta charset="utf-8">
<title>Parallax Studio – Business Card</title>
<link rel="stylesheet" href="https://fonts.googleapis.com/css2?family=Ubuntu:wght@400;500;700&family=Open+Sans:wght@400;600&display=swap">
<style>
  :root {
    --backdrop: #3b3b3d;
    --card: #1c1c1e;
    --gold: #c9a13b;
    --gold-light: #e3c46a;
    --silver: #b9b9bd;
    --white: #f4f4f4;
  }
  * { box-sizing: border-box; margin: 0; padding: 0; }
  html, body { width: 799px; height: 1200px; overflow: hidden; }
  body {
    background: var(--backdrop);
    display: flex;
    flex-direction: column;
    align-items: center;
    justify-content: center;
    gap: 110px;
  }
  .card {
    width: 680px;
    height: 390px;
    background: var(--card);
    border-radius: 4px;
    box-shadow: 0 14px 30px rgba(0,0,0,0.45);
    position: relative;
  }

  /* Front */
  .card--front {
    display: flex;
    flex-direction: column;
    align-items: center;
    justify-content: center;
  }
  .front-brand {
    display: flex;
    align-items: center;
    gap: 18px;
    font-family: "Ubuntu", sans-serif;
    font-weight: 500;
    font-size: 46px;
    letter-spacing: 4px;
    color: var(--silver);
    text-transform: uppercase;
  }
  .front-brand .brand-dot {
    width: 22px; height: 22px;
    border-radius: 50%;
    border: 3px solid var(--silver);
  }
  .front-url {
    margin-top: 48px;
    font-family: "Open Sans", sans-serif;
    font-size: 17px;
    letter-spacing: 3px;
    color: var(--gold);
  }

  /* Back */
  .card--back {
    display: flex;
    align-items: center;
    padding: 0 40px;
  }
  .back-brand {
    width: 250px;
    display: flex;
    flex-direction: column;
    align-items: center;
  }
  .back-brand .brand-name {
    font-family: "Ubuntu", sans-serif;
    font-weight: 500;
    font-size: 28px;
    letter-spacing: 4px;
    color: var(--gold);
    text-transform: uppercase;
  }
  .back-brand .brand-tagline {
    margin-top: 8px;
    font-family: "Ubuntu", sans-serif;
    font-weight: 700;
    font-size: 10.5px;
    letter-spacing: 2px;
    color: var(--gold);
  }
  .divider {
    width: 2px;
    height: 250px;
    margin: 0 36px 0 30px;
    background: linear-gradient(var(--gold-light), var(--gold));
  }
  .contact { font-family: "Ubuntu", sans-serif; }
  .contact-name {
    font-weight: 700;
    font-size: 25px;
    color: var(--gold);
  }
  .contact-role {
    font-size: 18px;
    color: var(--white);
    margin-bottom: 26px;
  }
  .contact-list { list-style: none; }
  .contact-list li {
    display: flex;
    align-items: center;
    gap: 14px;
    font-size: 17px;
    color: var(--white);
    line-height: 28px;
  }
  .contact-list svg { width: 16px; height: 16px; flex: none; }
  .contact-address {
    margin-top: 2px;
    font-size: 17px;
    color: var(--white);
  }
</style>
</head>
<body>

  <section class="card card--front">
    <div class="front-brand"><span class="brand-dot"></span>Parallax Studio</div>
    <div class="front-url">www.parallaxstudio.com.au</div>
  </section>

  <section class="card card--back">
    <div class="back-brand">
      <div class="brand-name">Parallax Studio</div>
      <div class="brand-tagline">Architecture Corporate Commercial</div>
    </div>
    <div class="divider"></div>
    <div class="contact">
      <div class="contact-name">Martin Hale</div>
      <div class="contact-role">Photographer</div>
      <ul class="contact-list">
        <li>
          <svg viewBox="0 0 16 16" aria-hidden="true"><path d="M3 2h3l1.5 3.5-2 1.2a8 8 0 0 0 3.8 3.8l1.2-2L14 10v3a1 1 0 0 1-1 1A11 11 0 0 1 2 3a1 1 0 0 1 1-1z" fill="var(--gold)"/></svg>
          0412587306
        </li>
        <li>
          <svg viewBox="0 0 16 16" aria-hidden="true"><rect x="1" y="3" width="14" height="10" fill="var(--gold)"/><path d="M1 3l7 6 7-6" fill="none" stroke="var(--card)" stroke-width="1.3"/></svg>
          info@parallaxstudio.com.au
        </li>
        <li>
          <svg viewBox="0 0 16 16" aria-hidden="true"><circle cx="8" cy="8" r="7" fill="var(--gold)"/><g fill="none" stroke="var(--card)" stroke-width="1"><ellipse cx="8" cy="8" rx="3" ry="7"/><path d="M1 8h14M2.5 4.5h11M2.5 11.5h11"/></g></svg>
          www.parallaxstudio.com.au
        </li>
      </ul>
      <div class="contact-address">27 Bay Rd Portland Vic 3305</div>
    </div>
  </section>

</body>
</html>
```